Lantern Petals Website v.1 - attract floral shop franchisees

I need a simple information website for my new business. We are a franchisor of flower shops. The overall purpose of the website is to promote the company and the service, especially to potential franchisees and retailers. Only about 4 pages are required including homepage, About, For Supermarkets, For Franchisees, and Contact. No special functions are required except the site will have two separate inquiry forms that must be filled out online and submitted via automated email. Similarly, an email form should be linked from the Contact page. I have a logo and business cards designed by ArtMingle, and I would like the site to have a consistent color scheme and style. The key to design will be to express the joy and love associated with flowers and floral bouquets.
IMPORTANT - I will be exporting the website design to Wordpress CMS in a site hosted by HostNimbus. For smooth integration into WordPress hosted by HostNimbus, the designer should build the site using a WordPress-friendly format. Ideally, they should use HTML, CSS, and PHP. Creating a custom theme or using a page builder that exports to WordPress-compatible files is best. This ensures the site can be easily imported and managed within WordPress.

Target Market(s)

Potential franchisees (existing florists or creative types who might like to own a floral business) and supermarkets who might want us to run their floral department

Industry/Entity Type

Floral retailing

Requirements
Must have
• A brand theme that is beautiful, consistent throughout and builds on the logo design
Nice to have
• Show gender and ethnic diversity in customers and florists. Pictures of happy florists (for franchisees) and pictures of amazing floral department displays (for supermarkets)

```html
<!DOCTYPE html>
<html lang="en">
<head>
<meta charset="utf-8">
<title>Lantern Petals – Homepage and Menu</title>
<link href="https://fonts.googleapis.com/css2?family=Great+Vibes&family=Roboto:wght@400;500&display=swap" rel="stylesheet">
<style>
:root{
  --gold:#f0ae2e;
  --gold-deep:#e39d1c;
  --green:#1f8a3c;
  --green-bright:#2fb36a;
  --pink:#fde0f8;
  --ink:#222;
  --body:#555;
  --white:#fff;
  --stage-bg:#ffffff;
}
*{box-sizing:border-box;margin:0;padding:0}
html,body{width:850px;height:1200px;overflow:hidden;background:var(--stage-bg)}
body{font-family:'Roboto',Arial,sans-serif;color:var(--ink)}
.stage{position:absolute;left:0;top:0;width:1625px;height:2300px;transform:scale(0.5217);transform-origin:0 0}
.abs{position:absolute}
.script{font-family:'Great Vibes',cursive}
.page{position:absolute;left:57px;top:44px;width:686px;height:2204px;background:var(--white);overflow:hidden;box-shadow:0 0 14px rgba(0,0,0,.08)}
.photo{position:absolute}
/* hero */
.hero-photo{left:0;top:0;width:686px;height:510px;background:radial-gradient(circle at 60% 45%,#f5b531 0,#e07a25 22%,#8a6d3a 45%,#3f5a3a 70%,#243326 100%)}
.hero-waves{position:absolute;left:0;top:0}
.logo-tab{position:absolute;left:64px;top:0;width:124px;height:78px;background:var(--white);display:flex;align-items:center;justify-content:center;gap:5px;box-shadow:0 2px 6px rgba(0,0,0,.08)}
.logo-dot{width:14px;height:14px;border-radius:50%;background:var(--gold)}
.logo-name{font-family:'Roboto',sans-serif;font-weight:500;font-size:13px;color:var(--gold-deep)}
.menu-btn{position:absolute;left:590px;top:22px;width:32px;height:32px;border-radius:50%;background:var(--gold);display:flex;flex-direction:column;justify-content:center;align-items:center;gap:4px}
.menu-btn span{display:block;width:16px;height:2px;background:#333}
.hero-kicker{position:absolute;left:0;width:686px;top:155px;text-align:center;color:var(--white);letter-spacing:4px;font-size:12px}
.hero-title{position:absolute;left:0;width:686px;top:165px;text-align:center;color:var(--white);font-size:64px}
.hero-btn{position:absolute;left:263px;top:244px;width:158px;height:28px;border-radius:14px;background:var(--white);border:2px solid var(--gold);font-size:8.5px;font-weight:500;display:flex;align-items:center;justify-content:center}
/* section heads */
.mark{position:absolute;width:40px;height:40px;border-radius:50%;border:2px solid var(--gold);background:var(--white)}
.mark::after{content:"";position:absolute;left:13px;top:6px;width:10px;height:10px;border-radius:50%;background:var(--gold)}
.eyebrow{position:absolute;left:0;width:686px;text-align:center;color:var(--green);letter-spacing:4px;font-size:12px;font-weight:500}
.heading{position:absolute;left:0;width:686px;text-align:center;color:var(--gold);font-size:44px}
.rule{position:absolute;height:2px;background:var(--green);opacity:.6}
/* about */
.partner-badge{position:absolute;left:62px;top:598px;width:95px;height:80px;border-radius:50%;background:radial-gradient(circle,#e8c27a,#c9953a)}
.about-photo{left:109px;top:632px;width:228px;height:208px;background:linear-gradient(160deg,#9fb0a4,#6f7d73 45%,#e6c43c 75%,#5e6a3e)}
.about-text{position:absolute;left:350px;top:636px;width:285px;font-size:8.6px;line-height:15.7px;color:var(--body)}
.about-text p+p{margin-top:15.7px}
.btn-outline{position:absolute;height:26px;border-radius:13px;border:2px solid var(--green);color:var(--green);font-size:8.5px;font-weight:500;display:flex;align-items:center;justify-content:center;background:var(--white)}
/* cards */
.gallery-bg{left:0;top:1150px;width:686px;height:850px;background:linear-gradient(180deg,#fff 0,#d8c4b8 12%,#b79a8d 40%,#c9a070 70%,#b98f63 100%);opacity:.85}
.flowers-top{left:250px;top:868px;width:180px;height:45px;background:linear-gradient(90deg,#d6c1e8,#b58fd3,#d9c9ea);border-radius:40% 40% 10% 10%;opacity:.8}
.card{position:absolute;top:890px;width:273px;height:358px;border-radius:10px;padding:32px 18px 0;text-align:center}
.card-super{left:64px;background:var(--gold);border-bottom:4px solid var(--green);transform:skewY(2deg);transform-origin:left top}
.card-super>*{transform:skewY(-2deg)}
.card-fran{left:350px;background:var(--white);border:1.5px solid var(--green)}
.card-title{font-size:36px;color:#333;line-height:1}
.card-fran .card-title{color:var(--green)}
.card-rule{width:70px;height:1.5px;background:#7a5b12;margin:10px auto 14px}
.card-fran .card-rule{background:var(--green)}
.card-text{font-size:8.5px;line-height:15.7px;color:#3a3a3a}
.card-fran .card-text{color:var(--body)}
.card-btn{display:inline-flex;margin-top:18px;width:156px;height:28px;border-radius:14px;border:2px solid var(--green);font-size:8.5px;font-weight:500;align-items:center;justify-content:center;background:var(--gold)}
.card-fran .card-btn{background:var(--white);margin-top:10px}
.card-medal{left:322px;top:1045px}
.card-floral{left:568px;top:1170px;width:50px;height:72px;background:linear-gradient(#e9a3a0,#f3d2c8);border-radius:40%;opacity:.8}
/* gallery */
.gallery-circle{position:absolute;left:198px;top:1255px;width:290px;height:290px;border-radius:50%;background:var(--white)}
.g-photo{position:absolute;width:104px;height:116px}
.btn-gold{position:absolute;left:264px;top:1682px;width:157px;height:26px;border-radius:13px;background:var(--gold);border:2px solid var(--green);font-size:8.5px;font-weight:500;display:flex;align-items:center;justify-content:center}
/* contact */
.contact-shape{position:absolute;left:0;top:1720px}
.contact-art{left:80px;top:1845px;width:250px;height:100px;background:linear-gradient(90deg,#3f6a2f,#b24a1f,#e5702a,#3f6a2f);border-radius:50%;opacity:.55}
.contact-title{position:absolute;left:90px;width:240px;top:1870px;text-align:center;color:var(--white);font-size:44px}
.contact-sub{position:absolute;left:60px;width:300px;top:1952px;text-align:center;color:var(--white);font-size:19px}
.contact-mail{position:absolute;left:60px;top:1988px;color:var(--white);font-size:17.5px}
.brand-circle{position:absolute;left:392px;top:1765px;width:230px;height:230px;border-radius:50%;background:var(--white);display:flex;align-items:center;justify-content:center;gap:10px}
.brand-circle .logo-dot{width:30px;height:30px}
.brand-circle .logo-name{font-size:30px}
/* footer */
.socials{display:flex;gap:6px;justify-content:center}
.social{width:13px;height:13px;border-radius:3px;background:#222}
.social.round{border-radius:50%;background:#3b5bdb}
.social.wide{width:18px;background:#d33}
.footer-social{position:absolute;left:0;width:686px;top:2112px}
.footer-links{position:absolute;left:0;width:686px;top:2143px;text-align:center;font-size:8.5px;color:#333;word-spacing:2px}
.footer-links span{margin:0 16px}
.footer-copy{position:absolute;left:0;width:686px;top:2170px;text-align:center;font-size:8.5px;color:#333}
/* menu board */
.menu-board{position:absolute;left:881px;top:44px;width:686px;height:376px;background:var(--pink);overflow:hidden;box-shadow:0 0 14px rgba(0,0,0,.08)}
.hex{position:absolute;width:98px;height:110px;clip-path:polygon(50% 0,100% 25%,100% 75%,50% 100%,0 75%,0 25%)}
.menu-logo{left:281px}
.menu-close{position:absolute;left:608px;top:32px}
.menu-list{position:absolute;left:191px;width:300px;top:106px;list-style:none;text-align:center}
.menu-list li{font-size:14.5px;font-weight:500;height:39.2px;color:#111}
.menu-social{position:absolute;left:0;width:686px;top:306px}
.tulips{left:0;top:300px;width:686px;height:76px;background:linear-gradient(180deg,rgba(253,224,248,0),#f1b6d3 40%,#e58fb6 80%,#7fb561)}
.arrow{position:absolute;left:760px;top:78px}
</style>
</head>
<body>
<div class="stage">

  <!-- Homepage -->
  <main class="page">
    <div class="photo hero-photo" role="img" aria-label="Close-up of a colourful bouquet with orange proteas, yellow orchids and greenery"></div>
    <svg class="hero-waves" width="686" height="520" viewBox="0 0 686 520">
      <path d="M0 470 C140 430 300 455 420 488 C520 512 620 505 686 492 L686 520 L0 520 Z" fill="#fff"/>
      <path d="M0 395 C130 330 270 370 380 435 C480 490 600 505 686 490 L686 502 C600 515 480 508 380 478 C270 445 140 420 0 470 Z" fill="#f0ae2e"/>
      <path d="M0 470 C60 420 200 405 300 455 C200 435 90 440 0 478 Z" fill="#1f8a3c"/>
    </svg>
    <div class="logo-tab"><span class="logo-dot"></span><span class="logo-name">Lantern Petals</span></div>
    <div class="menu-btn"><span></span><span></span><span></span></div>
    <div class="hero-kicker">WELCOME TO</div>
    <div class="hero-title script">Lantern Petals</div>
    <div class="hero-btn">FOR FRANCHISEES QUESTIONS?</div>

    <div class="mark" style="left:323px;top:505px"></div>
    <div class="eyebrow" style="top:560px">ABOUT US</div>
    <div class="heading script" style="top:572px">Lantern Petals</div>
    <div class="rule" style="left:298px;top:626px;width:90px"></div>

    <div class="partner-badge"></div>
    <div class="photo about-photo" role="img" aria-label="Smiling founder standing behind a table of bright bouquets"></div>
    <div class="about-text">
      <p>Fresh flowers convey special sentiments - love, happiness, joy – which every person deserves. Lantern Petals is an entrepreneurial company created to make top quality fresh flowers and artisan-designed bouquets accessible to every consumer at affordable prices.</p>
      <p>Lantern Petals brings the best of professional florists and supermarkets together for the benefit of consumers. It supports a national network of franchisees who own and operate the floral departments of some of the country's most progressive supermarkets, selling the finest floral stems and bouquets to customers at the market's best value.</p>
    </div>
    <div class="btn-outline" style="left:350px;top:806px;width:128px">MORE ABOUT US</div>

    <div class="photo gallery-bg" role="img" aria-label="Soft blurred view of a flower shop with roses in vases"></div>
    <div class="photo flowers-top" role="img" aria-label="Sprig of purple wildflowers"></div>

    <section class="card card-super">
      <h2 class="card-title script">For Supermarkets</h2>
      <div class="card-rule"></div>
      <p class="card-text">Supermarket flower departments benefit from high customer footfall, economies of scale and low pricing. However their quality of stems and bouquets is often poor and in-store service is limited. In contrast, professional florists typically sell the finest quality stems, design the most beautiful bouquets and provide the finest customer service, but their costs and customer prices are high. Supermarkets find that Lantern Petals, through their florist franchise network, is able to improve their financial outcomes, provide attentive customer service and satisfaction, and lift the quality of the entire store environment.</p>
      <span class="card-btn">MORE FOR SUPERMARKETS</span>
    </section>
    <section class="card card-fran">
      <h2 class="card-title script">For Franchisees</h2>
      <div class="card-rule"></div>
      <p class="card-text">Lantern Petals supports a national network of owner-operator franchisees with comprehensive services to enhance franchise profits. Our franchisees are the cornerstone of our business. Many of them are already professional florists or florist employees who wish to expand their businesses without the significant costs of a traditional flower shop. Others are creative types or flower lovers who have made a career change in order to express their talents and make people happy. Still others are entrepreneurs in search of owning their own business. All are welcome if they meet Lantern Petals' high standards of quality, service and ethical business practices.</p>
      <span class="card-btn">MORE FOR FRANCHISEES</span>
    </section>
    <div class="mark card-medal" style="width:44px;height:44px"></div>
    <div class="photo card-floral" role="img" aria-label="Small watercolour floral spray"></div>

    <div class="gallery-circle"></div>
    <div class="mark" style="left:323px;top:1335px"></div>
    <div class="eyebrow" style="top:1393px">LANTERN PETALS</div>
    <div class="heading script" style="top:1405px">Our Gallery</div>
    <div class="rule" style="left:306px;top:1471px;width:74px"></div>
    <div class="g-photo" style="left:6px;top:1512px;background:linear-gradient(150deg,#7a5a3c,#d9a73a,#4d3a2a)" role="img" aria-label="Florist arranging flowers on a workbench"></div>
    <div class="g-photo" style="left:120px;top:1492px;background:linear-gradient(160deg,#c8b08e,#e8d4c0,#d78fa0)" role="img" aria-label="Happy florist holding a bouquet"></div>
    <div class="g-photo" style="left:234px;top:1534px;background:linear-gradient(160deg,#6e4a2e,#a98468,#5b4a3e)" role="img" aria-label="Shop owner with an arrangement"></div>
    <div class="g-photo" style="left:348px;top:1484px;background:linear-gradient(180deg,#b9c1c3,#4f7a4a 50%,#b2343a)" role="img" aria-label="Greenhouse rows of red flowers"></div>
    <div class="g-photo" style="left:462px;top:1542px;background:linear-gradient(160deg,#e9e4de,#d85e8e,#3c6a38)" role="img" aria-label="Pink and white rose bouquet"></div>
    <div class="g-photo" style="left:576px;top:1500px;background:linear-gradient(160deg,#d8c6bc,#c25d7a,#2f3a2c)" role="img" aria-label="Supermarket floral display"></div>
    <div class="btn-gold">MORE OUR GALLERY</div>

    <svg class="contact-shape" width="686" height="370" viewBox="0 0 686 370">
      <path d="M0 60 C120 20 260 60 340 140 C380 190 420 240 520 260 C600 270 650 245 686 225 L686 364 L0 364 Z" fill="#f0ae2e"/>
      <path d="M0 38 C120 10 250 40 345 180 C260 80 140 40 0 60 Z" fill="#2fb36a"/>
    </svg>
    <div class="photo contact-art" role="img" aria-label="Painted floral garland behind the heading"></div>
    <div class="contact-title script">Contact Us</div>
    <div class="contact-sub script">For questions and further information,</div>
    <div class="contact-mail">Contact: info@lantern-petals.com</div>
    <div class="brand-circle"><span class="logo-dot"></span><span class="logo-name">Lantern Petals</span></div>

    <div class="footer-social socials"><i class="social round"></i><i class="social"></i><i class="social"></i><i class="social"></i><i class="social wide"></i></div>
    <nav class="footer-links">About Us<span>|</span>For Supermarkets<span>|</span>For Franchisees<span>|</span>Our Gallery<span>|</span>Contact Us</nav>
    <div class="footer-copy">Lantern Petals © 2024 All Rights Reserved | Privacy Policy | Terms and Conditions</div>
  </main>

  <svg class="arrow" width="70" height="20" viewBox="0 0 70 20">
    <path d="M2 10 C25 6 45 8 66 10 M56 4 L66 10 L56 16" fill="none" stroke="#2fb36a" stroke-width="2"/>
  </svg>

  <!-- Menu overlay -->
  <aside class="menu-board">
    <div class="hex" style="left:-50px;top:18px;background:linear-gradient(#e7b7a8,#6f8a5a)" role="img" aria-label="Hands arranging flowers"></div>
    <div class="hex" style="left:79px;top:8px;background:linear-gradient(#e8d6c8,#4d6a9a)" role="img" aria-label="Florist in an apron with a bouquet"></div>
    <div class="hex" style="left:5px;top:100px;background:linear-gradient(#b8c1c5,#b2343a)" role="img" aria-label="Greenhouse rows"></div>
    <div class="hex" style="left:107px;top:100px;background:linear-gradient(#d0c4b4,#e28c8a)" role="img" aria-label="Florist wrapping a bouquet"></div>
    <div class="hex" style="left:56px;top:192px;background:linear-gradient(#8a8e88,#59606a)" role="img" aria-label="Shop owner in a greenhouse"></div>
    <div class="hex" style="left:532px;top:82px;background:linear-gradient(#bdc8c0,#e2b732)" role="img" aria-label="Founder with yellow flowers"></div>
    <div class="hex" style="left:482px;top:170px;background:linear-gradient(#d8658e,#e9a23a)" role="img" aria-label="Buckets of mixed flowers"></div>
    <div class="hex" style="left:583px;top:170px;background:linear-gradient(#f0eded,#d9437a)" role="img" aria-label="White and pink blooms"></div>
    <div class="hex" style="left:532px;top:258px;background:linear-gradient(#d9b59a,#b6612c)" role="img" aria-label="Two florists at work"></div>
    <div class="photo tulips" role="img" aria-label="Border of pink tulips"></div>
    <div class="logo-tab menu-logo"><span class="logo-dot"></span><span class="logo-name">Lantern Petals</span></div>
    <svg class="menu-close" width="16" height="16" viewBox="0 0 16 16"><path d="M2 2 L14 14 M14 2 L2 14" stroke="#2fb36a" stroke-width="1.5"/></svg>
    <ul class="menu-list">
      <li>ABOUT US</li><li>FOR SUPERMARKETS</li><li>FOR FRANCHISEES</li><li>OUR GALLERY</li><li>CONTACT US</li>
    </ul>
    <div class="menu-social socials"><i class="social"></i><i class="social"></i><i class="social"></i><i class="social wide"></i></div>
  </aside>

</div>
</body>
</html>
```